Business Cards - Brightpath Horizon

need to design unique business card for my mortgage business. I need to design credit card style business card for my business or any unique idea that you might have

Target Market(s)

Home Loan customers

Industry/Entity Type

Mortgage Brokerage

Contact Information for Business Card

please design credit card style or very unique style business card

Colors

Designer to choose colors to be used in the design.

Requirements
Must have
• Name
• position
• Phone number
• fax number
• email address
• website address
• social media address
• All above fields will be provided once design in finalised

```html
<!DOCTYPE html>
<html lang="en">
<head>
<meta charset="utf-8">
<title>Brightpath Horizon – Business Cards</title>
<link rel="stylesheet" href="https://fonts.googleapis.com/css2?family=Gelasio:wght@600&family=Open+Sans:wght@400&display=swap">
<style>
  :root {
    --stage: #222222;
    --card-white: #ffffff;
    --brand-blue: #1a38c2;
    --brand-orange: #f5831f;
    --ink: #222222;
    --rule-blue: #6fa7d6;
    --grad-orange: #f7871a;
    --grad-mid: #6c5a8a;
    --grad-blue: #0530d2;
    --white: #ffffff;
  }
  * { margin: 0; padding: 0; box-sizing: border-box; }
  html, body { width: 1200px; height: 900px; overflow: hidden; background: var(--stage); }
  .canvas { position: relative; width: 1200px; height: 900px; background: var(--stage); }

  .card {
    position: absolute; top: 306px; width: 440px; height: 271px;
    border-radius: 12px; box-shadow: 3px 4px 8px rgba(0,0,0,0.55);
  }
  .card-front { left: 149px; background: var(--card-white); }
  .card-back {
    left: 608px;
    background: linear-gradient(150deg, var(--grad-orange) 0%, var(--grad-mid) 45%, var(--grad-blue) 100%);
  }

  .brand-name {
    position: absolute; text-align: center;
    font-family: "Gelasio", serif; font-weight: 600; color: var(--brand-blue);
    line-height: 1.05; text-transform: uppercase;
  }
  .card-front .brand-name { left: 30px; top: 112px; width: 183px; font-size: 21px; letter-spacing: 0.5px; }
  .card-back .brand-name { left: 0; top: 100px; width: 440px; font-size: 36px; letter-spacing: 1px; }

  .divider { position: absolute; left: 235px; top: 87px; width: 1px; height: 97px; background: var(--rule-blue); }

  .contact { position: absolute; left: 256px; top: 84px; font-family: "Open Sans", sans-serif; }
  .person-name { font-family: "Gelasio", serif; font-weight: 600; font-size: 15px; color: var(--brand-orange); letter-spacing: 0.5px; line-height: 18px; }
  .person-role { font-size: 12px; color: var(--ink); line-height: 15px; }
  .contact-list { list-style: none; margin-top: 6px; }
  .contact-item { display: flex; align-items: center; font-size: 12px; color: var(--ink); line-height: 16px; }
  .contact-item svg { width: 9px; height: 9px; margin-right: 6px; fill: var(--brand-orange); flex: none; }

  .social { position: absolute; left: 118px; top: 230px; width: 205px; height: 20px; display: flex; align-items: center; }
  .social-rule { flex: 1; height: 1px; background: var(--white); }
  .social-icons { display: flex; gap: 6px; margin: 0 6px; }
  .social-icon { width: 18px; height: 18px; background: var(--white); }
</style>
</head>
<body>
<main class="canvas">

  <section class="card card-front" aria-label="Business card front">
    <div class="brand-name">Brightpath<br>Horizon</div>
    <div class="divider"></div>
    <div class="contact">
      <div class="person-name">MARCUS BELLAMY</div>
      <div class="person-role">Managing Director</div>
      <ul class="contact-list">
        <li class="contact-item">
          <svg viewBox="0 0 10 10" aria-hidden="true"><path d="M1 4 Q1 2 5 2 Q9 2 9 4 L7 4.5 L6.5 3.5 L3.5 3.5 L3 4.5 Z M2.5 5 L7.5 5 L8.5 8.5 L1.5 8.5 Z"/></svg>
          (044)555018274
        </li>
        <li class="contact-item">
          <svg viewBox="0 0 10 10" aria-hidden="true"><path d="M2 1 H6 L8 3 V9 H2 Z M3 5 H7 V5.8 H3 Z M3 6.8 H7 V7.6 H3 Z" fill-rule="evenodd"/></svg>
          (044)555018274
        </li>
        <li class="contact-item">
          <svg viewBox="0 0 10 10" aria-hidden="true"><path d="M1 2.5 H9 V8 H1 Z"/></svg>
          info@bphorizon.com
        </li>
        <li class="contact-item">
          <svg viewBox="0 0 10 10" aria-hidden="true"><circle cx="5" cy="5" r="4.2"/></svg>
          www.bphorizon.com
        </li>
      </ul>
    </div>
  </section>

  <section class="card card-back" aria-label="Business card back">
    <div class="brand-name">Brightpath<br>Horizon</div>
    <div class="social">
      <span class="social-rule"></span>
      <div class="social-icons">
        <span class="social-icon" role="img" aria-label="Social network profile"></span>
        <span class="social-icon" role="img" aria-label="Social network profile"></span>
        <span class="social-icon" role="img" aria-label="Social network profile"></span>
      </div>
      <span class="social-rule"></span>
    </div>
  </section>

</main>
</body>
</html>
```